Communication and Marketing agency needs a new presentation card

We are a group of communication and marketing agencies specialized in companies that are in the logistics and industrial sector. The head agency is TELVANO Grupo and the group consists of 4 agencies: TELVANO Media, TELVANO Digital, TELVANO Research and DifundeEnPantalla. We hace 4 offices in Spain (Madrid, Barcelona, Valencia and Murcia). We are looking for a clean and attractive design that transmits our experience, brand presence in the market and knowledge to those who receive the card.It has to maintain the colors of the logo that is attached.
Target Market(s)
logistics and industrial sector
Marketing department
Contact Information for Business Card
Clean and attractive design

```html
<!DOCTYPE html>
<html lang="es">
<head>
<meta charset="utf-8">
<title>TELVANO Grupo – Tarjeta de presentación</title>
<link rel="stylesheet" href="https://fonts.googleapis.com/css2?family=Open+Sans:wght@400;600&family=Roboto:wght@700&display=swap">
<style>
  :root {
    --backdrop: #5c5c5c;
    --card-white: #f3f3f3;
    --brand-red: #b01c27;
    --ink: #2b2b2b;
    --paper-text: #ffffff;
    --rule: rgba(255,255,255,0.75);
  }
  * { margin: 0; padding: 0; box-sizing: border-box; }
  html, body { width: 1200px; height: 900px; overflow: hidden; }
  body {
    background: var(--backdrop);
    font-family: "Open Sans", Arial, sans-serif;
    position: relative;
  }
  .card {
    position: absolute;
    top: 200px;
    width: 310px;
    height: 502px;
    box-shadow: 3px 4px 6px rgba(0,0,0,0.35);
  }
  .card--front {
    left: 253px;
    background: var(--card-white);
    border-radius: 58px 0 58px 0;
  }
  .card--back {
    left: 627px;
    background: var(--brand-red);
    border-radius: 0 58px 0 58px;
    color: var(--paper-text);
  }
  .wordmark {
    position: absolute;
    left: 0; right: 0;
    text-align: center;
    font-weight: 600;
    line-height: 1.05;
  }
  .card--front .wordmark {
    top: 122px;
    color: var(--brand-red);
    font-size: 40px;
    letter-spacing: 1px;
  }
  .card--back .wordmark {
    top: 160px;
    color: var(--paper-text);
    font-size: 42px;
    letter-spacing: 1px;
  }
  .wordmark small { display: block; font-size: 26px; letter-spacing: 0; }
  .holder {
    position: absolute;
    left: 32px;
    top: 302px;
    color: var(--ink);
  }
  .holder__name {
    font-family: "Roboto", Arial, sans-serif;
    font-weight: 700;
    font-size: 19px;
    color: var(--brand-red);
    line-height: 24px;
  }
  .holder__role { font-size: 14.5px; line-height: 20px; }
  .contact-list { list-style: none; margin-top: 6px; }
  .contact-list li {
    display: flex;
    align-items: center;
    font-size: 14.5px;
    line-height: 18.3px;
  }
  .contact-list svg { width: 12px; height: 12px; margin-right: 7px; fill: var(--brand-red); }
  .holder__address { font-size: 14.5px; line-height: 18.5px; margin-top: 6px; }
  .offices {
    position: absolute;
    top: 262px;
    left: 0; right: 0;
    text-align: center;
    font-size: 14.5px;
  }
  .divider {
    position: absolute;
    top: 347px;
    left: 35px;
    width: 239px;
    border-top: 1px solid var(--rule);
  }
  .agencies {
    position: absolute;
    top: 376px;
    left: 36px;
    width: 244px;
    display: grid;
    grid-template-columns: 1fr 1fr;
    row-gap: 20px;
    column-gap: 12px;
  }
  .agency {
    font-weight: 600;
    font-size: 14px;
    line-height: 1.1;
    text-align: center;
  }
  .agency small { display: block; font-size: 10px; }
</style>
</head>
<body>
  <section class="card card--front">
    <div class="wordmark">TELVANO<small>Grupo</small></div>
    <div class="holder">
      <p class="holder__name">MARCOS FERRER</p>
      <p class="holder__role">Managing Director</p>
      <ul class="contact-list">
        <li><svg viewBox="0 0 12 12" aria-hidden="true"><path d="M1 4.5C1 2.5 3 1.5 6 1.5S11 2.5 11 4.5L9 5 8.5 3.8h-5L3 5ZM2.5 6h7l1 4.5h-9ZM6 6.8a1.6 1.6 0 1 0 0 3.2 1.6 1.6 0 0 0 0-3.2Z"/></svg>044-870 312 546</li>
        <li><svg viewBox="0 0 12 12" aria-hidden="true"><path d="M3.5 0.5h5a1 1 0 0 1 1 1v9a1 1 0 0 1-1 1h-5a1 1 0 0 1-1-1v-9a1 1 0 0 1 1-1Zm0.5 1.5v7h4v-7ZM6 9.5a0.6 0.6 0 1 0 0 1.2 0.6 0.6 0 0 0 0-1.2Z"/></svg>044-870 312 546</li>
        <li><svg viewBox="0 0 12 12" aria-hidden="true"><path d="M0.5 2.5h11v7h-11Zm1 1 4.5 3.2 4.5-3.2Z"/></svg>info@telvano-mail.com</li>
        <li><svg viewBox="0 0 12 12" aria-hidden="true"><circle cx="6" cy="6" r="5.5"/><path d="M3 4.5 5 3.5 6.5 5 5 7.5 3.5 6.5Zm4.5 3 2-1-0.5 2.5-1.5 1Z" fill="#f3f3f3"/></svg>www.telvanogrupo.net</li>
      </ul>
      <p class="holder__address">28014, Calle Lirio 27<br>Madrid, España, 28014.</p>
    </div>
  </section>

  <section class="card card--back">
    <div class="wordmark">TELVANO<small>Grupo</small></div>
    <p class="offices">Madrid, Barcelona, Valencia, Murcia</p>
    <div class="divider"></div>
    <div class="agencies">
      <p class="agency">TELVANO<small>Research</small></p>
      <p class="agency">TELVANO<small>Digital</small></p>
      <p class="agency">TELVANO<small>Media</small></p>
      <p class="agency">DifundeEn<small>Pantalla</small></p>
    </div>
  </section>
</body>
</html>
```